Healthy lifestyle Influencer business card

I need your creativity to have a business card that I can leave in all the restaurants, hotels and spas I visit to inform them that I am an influencer specializing in the wellness sector and that I will write a review about them. You can use my instagram photos Lunavita27 or on my website www.piattileggeriorto.it. I would like my business card to impress with its creativity! thank you very much!

Contact Information for Business Card

siteweb, instagram, phone number

Font styles to use
Decorative
Script

Colors
0094D4
00A9DD
6FCCEA
C7EBF8
E9F6FB
59FF00
82FF00
B8FF75
E3FFCB
F4FFEA
FFC000
F8CF3A
FAE287
FDF2CF
FEFAEE
F0912C
F2A743
F7CA91
FBE8D2
FDF5EE
EE7325
F08F49
F5BC92
FAE3D3
FDF4ED
EB3D1F
EC4F4E
F09395
F8D3D4
FCEDEE
E54698
E96AAD
F1A4CE
F9D9EA
FCEFF6

Requirements
Nice to have
• creativity

```html
<!DOCTYPE html>
<html lang="it">
<head>
<meta charset="utf-8">
<title>Luna Vita Chef – Biglietto da visita</title>
<link rel="stylesheet" href="https://fonts.googleapis.com/css2?family=Manrope:wght@400;600;800&display=swap">
<style>
  :root{
    --page:#e9e4dc;
    --card-front:#1f1f1f;
    --card-back:#2a2320;
    --accent:#f2a743;
    --cream:#f1d9c2;
    --text:#f4f1ec;
    --muted:#cfc8bf;
    --photo-a:#e8c79a;
    --photo-b:#b07a45;
  }
  *{box-sizing:border-box;margin:0;padding:0}
  html,body{width:1200px;height:768px;overflow:hidden;background:var(--page);font-family:"Manrope",sans-serif}
  .canvas{position:relative;width:1200px;height:768px}
  .card{position:absolute;top:229px;width:540px;height:310px;border-radius:22px;overflow:hidden;box-shadow:0 14px 30px rgba(0,0,0,.25)}
  .card--front{left:40px;background:var(--card-front)}
  .card--back{left:620px;background:radial-gradient(ellipse at 45% 45%,#4a3a30 0%,#2f2622 55%,var(--card-back) 100%)}

  .photo{position:absolute;border-radius:50%;border:5px solid #fff}
  .photo--large{left:26px;top:120px;width:150px;height:150px;background:radial-gradient(circle at 40% 40%,#f3e2cb 0%,var(--photo-a) 45%,var(--photo-b) 100%)}
  .photo--small{left:120px;top:38px;width:96px;height:96px;background:radial-gradient(circle at 50% 45%,#f5d9a0 0%,#e1a664 60%,#c9c3bd 100%)}

  .brand{position:absolute;display:flex;flex-direction:column;align-items:center;color:var(--text)}
  .brand__row{display:flex;align-items:center;gap:10px}
  .brand__dot{width:14px;height:14px;border-radius:50%;background:var(--cream)}
  .brand__name{font-weight:600;letter-spacing:.04em;color:var(--text)}
  .brand__tagline{font-weight:400;color:var(--muted)}
  .card--front .brand{left:250px;top:46px;width:250px}
  .card--front .brand__name{font-size:26px}
  .card--front .brand__tagline{font-size:11px;margin-top:6px}

  .person{position:absolute;left:236px;top:118px}
  .person__name{font-size:17px;font-weight:800;color:var(--accent);letter-spacing:.02em}
  .person__role{font-size:11px;color:var(--muted);margin-top:2px}

  .divider{position:absolute;left:236px;right:24px;top:160px;height:1px;background:var(--accent)}

  .contacts{position:absolute;left:236px;top:176px;list-style:none;font-size:11px;color:var(--text)}
  .contacts li{display:flex;align-items:center;gap:8px;margin-bottom:6px;white-space:nowrap}
  .contacts svg{width:12px;height:12px;flex:none}

  .address{position:absolute;right:24px;top:176px;text-align:right;font-size:11px;line-height:1.6;font-style:normal;color:var(--text);white-space:nowrap}

  .card--back .brand{left:0;right:0;top:110px}
  .card--back .brand__name{font-size:40px}
  .card--back .brand__dot{width:20px;height:20px}
  .card--back .brand__tagline{font-size:14px;margin-top:10px}
</style>
</head>
<body>
<main class="canvas">

  <section class="card card--front">
    <div class="photo photo--small" role="img" aria-label="Foto di un muffin ai mirtilli"></div>
    <div class="photo photo--large" role="img" aria-label="Foto di una fetta di cheesecake con cioccolato"></div>

    <div class="brand">
      <div class="brand__row"><span class="brand__dot"></span><span class="brand__name">Luna Vita Chef</span></div>
      <span class="brand__tagline">sano e buono ogni giorno</span>
    </div>

    <div class="person">
      <p class="person__name">MARCO BELLINI</p>
      <p class="person__role">President</p>
    </div>

    <div class="divider"></div>

    <ul class="contacts">
      <li><svg viewBox="0 0 24 24"><path fill="#f2a743" d="M6.6 10.8a15.1 15.1 0 0 0 6.6 6.6l2.2-2.2a1 1 0 0 1 1-.25 11.4 11.4 0 0 0 3.6.57 1 1 0 0 1 1 1V20a1 1 0 0 1-1 1A17 17 0 0 1 3 4a1 1 0 0 1 1-1h3.5a1 1 0 0 1 1 1c0 1.25.2 2.45.57 3.57a1 1 0 0 1-.25 1z"/></svg>555.204.3318</li>
      <li><svg viewBox="0 0 24 24"><rect x="2" y="5" width="20" height="14" rx="2" fill="#f2a743"/><path d="M3 6l9 7 9-7" fill="none" stroke="#1f1f1f" stroke-width="2"/></svg>info@piattileggeriorto.it</li>
      <li><svg viewBox="0 0 24 24"><rect x="3" y="3" width="18" height="18" rx="5" fill="none" stroke="#f2a743" stroke-width="2"/><circle cx="12" cy="12" r="4" fill="none" stroke="#f2a743" stroke-width="2"/></svg>@Lunavita27</li>
    </ul>

    <address class="address">
      42 Willow Court<br>
      Nome, Alaska 99762<br>
      www.piattileggeriorto.it
    </address>
  </section>

  <section class="card card--back" role="img" aria-label="Foto scura di un dolce al cioccolato sullo sfondo">
    <div class="brand">
      <div class="brand__row"><span class="brand__dot"></span><span class="brand__name">Luna Vita Chef</span></div>
      <span class="brand__tagline">sano e buono ogni giorno</span>
    </div>
  </section>

</main>
</body>
</html>
```